Labour Day banner showcasing 20% off site

Banner graphic promoting our Labour Day sale
Size: 2000px x 600px
- examples from other companies and their sale banners have been uploaded for inspiration. Labour day examples are for the United States's holiday and submissions should NOT be in their country colours.
- product images can be found at www.flormaplex.com

Target Market(s)

19+

Industry/Entity Type

Cannabis

Requirements
Must have
• Phrases:
- “Happy Labour Day”
- “20% off site wide sale*"
- "Coupon code: Kestrel20"
- Underneath phrase the date of sale “September 3rd - 7th”
- In tiny print “*excludes all sale and bundled items”
- MUST BE 2000px x 600px
Nice to have
• - images of the products or bud we carry which can be found at www.flormaplex.com
- bold
Should not have
• - company logo
- the American flag, we are a Canadian company, colours and flag should all be Canadian

```html
<!DOCTYPE html>
<html lang="en">
<head>
<meta charset="utf-8">
<title>Happy Labour Day – 20% Off Site Wide Sale</title>
<link href="https://fonts.googleapis.com/css2?family=Bungee&family=Montserrat:wght@400;700&family=Yellowtail&display=swap" rel="stylesheet">
<style>
  :root {
    --maple-red: #e21b23;
    --navy: #22305f;
    --white: #ffffff;
    --blush: #f6c9cb;
  }
  html, body {
    margin: 0;
    padding: 0;
    overflow: hidden;
    background: var(--white);
  }
  .banner {
    position: relative;
    width: 1200px;
    height: 360px;
    overflow: hidden;
    background: var(--white);
  }
  .banner svg {
    position: absolute;
    inset: 0;
    display: block;
  }
  .script-title {
    font-family: "Yellowtail", cursive;
    fill: var(--navy);
    stroke: var(--white);
    stroke-width: 6px;
    stroke-linejoin: round;
    paint-order: stroke fill;
  }
  .headline {
    font-family: "Bungee", sans-serif;
    fill: var(--white);
  }
  .sale-dates {
    font-family: "Montserrat", sans-serif;
    font-weight: 700;
    fill: var(--white);
  }
  .coupon-label {
    font-family: "Montserrat", sans-serif;
    font-weight: 400;
    fill: var(--maple-red);
  }
  .coupon-code {
    font-family: "Bungee", sans-serif;
    fill: var(--maple-red);
  }
  .fine-print {
    font-family: "Montserrat", sans-serif;
    font-weight: 700;
    fill: var(--white);
  }
</style>
</head>
<body>
<main class="banner">
  <svg width="1200" height="360" viewBox="0 0 1200 360" xmlns="http://www.w3.org/2000/svg">
    <defs>
      <linearGradient id="leafSpray" x1="0" y1="0" x2="1" y2="1">
        <stop offset="0" stop-color="#f4b3b6"/>
        <stop offset="1" stop-color="#ea5a60"/>
      </linearGradient>
      <radialGradient id="leafBurst" cx="0.5" cy="0.5" r="0.5">
        <stop offset="0" stop-color="#e21b23"/>
        <stop offset="1" stop-color="#ee6b70"/>
      </radialGradient>
    </defs>

    <!-- left brushed red band -->
    <path class="brush-band-left" fill="var(--maple-red)"
          d="M0 0 H298 L250 60 L190 130 L160 170 L120 220 L70 270 L30 300 L0 318 Z"/>

    <!-- right red field -->
    <path class="red-field-right" fill="var(--maple-red)"
          d="M840 0 H1200 V360 H545 L620 270 L700 175 L760 100 L812 35 Z"/>

    <!-- leaf spray decoration on the red field -->
    <rect class="leaf-spray" role="img" aria-label="White cannabis leaf silhouettes scattered across the red field"
          x="640" y="20" width="235" height="340" rx="30" fill="url(#leafSpray)" opacity="0.55"/>

    <!-- leaf burst behind the title -->
    <ellipse class="leaf-burst" role="img" aria-label="Large red leaf illustration behind the holiday greeting"
             cx="405" cy="175" rx="200" ry="168" fill="url(#leafBurst)"/>

    <!-- holiday greeting -->
    <g class="greeting">
      <text class="script-title" x="428" y="118" font-size="66" text-anchor="middle">Happy</text>
      <text class="script-title" x="392" y="190" font-size="102" text-anchor="middle">Labour</text>
      <text class="script-title" x="418" y="282" font-size="100" text-anchor="middle">Day</text>
    </g>

    <!-- offer -->
    <g class="offer">
      <text class="headline" x="878" y="82" font-size="64" textLength="294" lengthAdjust="spacingAndGlyphs">20% OFF</text>
      <text class="headline" x="883" y="135" font-size="52" textLength="284" lengthAdjust="spacingAndGlyphs">SITE WIDE</text>
      <text class="headline" x="884" y="231" font-size="110" textLength="284" lengthAdjust="spacingAndGlyphs">SALE</text>

      <text class="sale-dates" x="889" y="264" font-size="20" textLength="271" lengthAdjust="spacingAndGlyphs">September 3<tspan font-size="11" dy="-8">rd</tspan><tspan dy="8"> - 7</tspan><tspan font-size="11" dy="-8">th</tspan><tspan dy="8">, 2020</tspan></text>

      <rect class="coupon-box" x="883" y="279" width="285" height="41" fill="var(--white)"/>
      <text x="896" y="307" font-size="18"><tspan class="coupon-label">Coupon Code : </tspan><tspan class="coupon-code" font-size="17">Kestrel20</tspan></text>

      <text class="fine-print" x="1168" y="337" font-size="9" text-anchor="end">*excludes all sale and bundled items</text>
    </g>
  </svg>
</main>
</body>
</html>
```